Nivel Crest - Powerpoint Templates

We are a consultancy to help builders to optimize their planning in order to save building costs. For that reason we need templates for teasers and presentations where we offer our services, show our team and their capacities and present workflows, organization charts, price lists etc.

```html
<!DOCTYPE html>
<html lang="en">
<head>
<meta charset="utf-8">
<title>Nivel Crest – Presentation Templates</title>
<link href="https://fonts.googleapis.com/css2?family=Signika:wght@400;600&family=Poppins:wght@400;500&family=Open+Sans:wght@400;600&display=swap" rel="stylesheet">
<style>
:root{
  --gold:#c0803a;
  --gold-light:#e6ac6a;
  --ink:#222;
  --grey:#6f6f6f;
  --ring:#dcdcdc;
  --paper:#fff;
}
*{box-sizing:border-box;margin:0;padding:0}
html,body{width:1200px;height:1111px;overflow:hidden;background:var(--paper)}
body{position:relative;font-family:'Open Sans',sans-serif;color:var(--ink)}
.slide{position:absolute;width:509px;height:286px;background:var(--paper);box-shadow:0 2px 10px rgba(0,0,0,.12);overflow:hidden}
.s1{left:70px;top:76px}.s2{left:619px;top:76px}
.s3{left:70px;top:408px}.s4{left:618px;top:408px}
.s5{left:70px;top:739px}.s6{left:619px;top:739px}
.title{position:absolute;top:3px;left:0;width:100%;text-align:center;font-family:'Signika',sans-serif;font-weight:600;font-size:17px}
.title::after{content:"";display:block;width:38px;height:1.5px;background:var(--gold);margin:3px auto 0}
.lead{position:absolute;top:38px;left:40px;right:40px;text-align:center;font-size:8.3px;line-height:11.5px}
.brand-mini{position:absolute;top:10px;right:10px;display:flex;align-items:center;gap:3px;font-family:'Signika',sans-serif;font-weight:600;font-size:8px;color:var(--ink)}
.brand-mini i,.brand i{display:block;background:var(--gold)}
.brand-mini i{width:8px;height:8px}
.footer{position:absolute;left:0;bottom:0;width:467px;height:17px;background:var(--gold);color:#fff;font-family:'Poppins',sans-serif;font-size:6px;line-height:17px;padding-left:9px}
.page{position:absolute;right:6px;bottom:0;height:17px;line-height:17px;font-family:'Poppins',sans-serif;font-size:6px}
/* cover */
.cover-pattern{position:absolute;inset:0;background:radial-gradient(ellipse at 10% 20%,#f1f1f1 0,transparent 40%),radial-gradient(ellipse at 90% 10%,#f3f3f3 0,transparent 35%),radial-gradient(ellipse at 20% 95%,#eeeeee 0,transparent 35%)}
.brand{position:absolute;left:60px;top:70px;display:flex;align-items:center;gap:10px;font-family:'Signika',sans-serif;font-weight:600;font-size:44px;color:#3a3a3a;letter-spacing:1px}
.brand i{width:30px;height:30px}
.cover-title{position:absolute;top:150px;width:100%;text-align:center;font-family:'Signika',sans-serif;font-weight:600;font-size:20px;color:#555}
.cover-sub{position:absolute;top:182px;width:100%;text-align:center;font-family:'Signika',sans-serif;font-size:12px}
/* services */
.service{position:absolute;top:83px;width:110px;margin-left:-55px;text-align:center}
.service svg{display:block;margin:0 auto}
.service h3{font-family:'Signika',sans-serif;font-weight:600;font-size:9.5px;margin-top:12px}
.service p{font-family:'Poppins',sans-serif;font-size:4.2px;line-height:7.5px;color:var(--grey);margin-top:4px;padding:0 6px}
/* about */
.about-photo{position:absolute;left:52px;top:69px;width:196px;height:181px;border:3px solid var(--gold);border-radius:3px;background:linear-gradient(135deg,#b9a58c,#5a4f48 55%,#d8cfc4)}
.about-text{position:absolute;left:265px;top:78px;width:213px;font-size:7px;line-height:11.1px;color:#444;text-align:justify}
.about-text p+p{margin-top:6px}
/* team */
.member{position:absolute;width:118px;height:83px;background:linear-gradient(180deg,#9aa6ad,#4a545b 70%,#1f2428)}
.member .name{position:absolute;left:9px;bottom:8px;color:#fff;font-family:'Poppins',sans-serif;font-size:5.6px;line-height:6px}
.member .role{display:block;font-size:3.6px;line-height:5px}
.member .tag{position:absolute;right:0;bottom:0;width:12px;height:12px;background:var(--gold)}
/* workflow */
.flow{position:absolute;left:0;top:0}
.flow-text{position:absolute;width:100px;margin-left:-50px;text-align:center;font-family:'Poppins',sans-serif;font-size:5px;line-height:9.3px;color:#555}
/* charts */
.chart{position:absolute;top:80px;width:140px;margin-left:-70px;text-align:center}
.chart p{font-family:'Poppins',sans-serif;font-size:6.8px;line-height:11.7px;color:#777;margin-top:7px}
.img-fill{display:block}
</style>
</head>
<body>

<section class="slide s1">
  <div class="cover-pattern" role="img" aria-label="Faint flowing line pattern in light grey"></div>
  <div class="brand"><i></i>NIVEL CREST</div>
  <div class="cover-title">Company Profile Title Here</div>
  <div class="cover-sub">Because Results Matter</div>
</section>

<section class="slide s2">
  <h2 class="title">Our Services</h2>
  <div class="brand-mini"><i></i>Nivel Crest</div>
  <p class="lead">Caonsectetur adipiscing elitsed do eiusmod tempor incididuntut labore et dolore magna aliqua.<br>Ut enim ad minim veniam.</p>
  <div class="service" style="left:79px">
    <svg width="96" height="106" viewBox="0 0 96 106" role="img" aria-label="Photo of business people in a meeting"><polygon points="48,2 94,28 94,78 48,104 2,78 2,28" fill="#7d7f80" stroke="#8a8a8a" stroke-width="3"/></svg>
    <h3>Consectet Yaradipisc</h3>
    <p>Planning review and cost checks that help every builder save money on site.</p>
  </div>
  <div class="service" style="left:196px">
    <svg width="96" height="106" viewBox="0 0 96 106" role="img" aria-label="Photo of a team working in an office"><polygon points="48,2 94,28 94,78 48,104 2,78 2,28" fill="#8f8a80" stroke="var(--gold)" stroke-width="3"/></svg>
    <h3>Consectet Yaradipisc</h3>
    <p>Planning review and cost checks that help every builder save money on site.</p>
  </div>
  <div class="service" style="left:313px">
    <svg width="96" height="106" viewBox="0 0 96 106" role="img" aria-label="Photo of three colleagues reviewing documents"><polygon points="48,2 94,28 94,78 48,104 2,78 2,28" fill="#5d6268" stroke="#8a8a8a" stroke-width="3"/></svg>
    <h3>Consectet Yaradipisc</h3>
    <p>Planning review and cost checks that help every builder save money on site.</p>
  </div>
  <div class="service" style="left:430px">
    <svg width="96" height="106" viewBox="0 0 96 106" role="img" aria-label="Photo of engineers in hard hats on a roof"><polygon points="48,2 94,28 94,78 48,104 2,78 2,28" fill="#4f6f92" stroke="var(--gold)" stroke-width="3"/></svg>
    <h3>Consectet Yaradipisc</h3>
    <p>Planning review and cost checks that help every builder save money on site.</p>
  </div>
  <div class="footer">www.nivelcrest.com</div><div class="page">Page 02</div>
</section>

<section class="slide s3">
  <h2 class="title">About Us</h2>
  <div class="brand-mini"><i></i>Nivel Crest</div>
  <p class="lead">Caonsectetur adipiscing elitsed do eiusmod tempor incididuntut labore et dolore magna aliqua.<br>Utenimad minim veniam.</p>
  <div class="about-photo" role="img" aria-label="Photo of an advisor with a couple at a laptop"></div>
  <div class="about-text">
    <p>Laerspiciatis unde omnis iste natus error sit voluptatem accusantium doloremque laudantium, totam rem aperiam, eaque ipsa quae ab illo inventore veritatis et quasi architecto beatae vitae dicta sunt explicabo. Nemo enim ipsam voluptatem quia voluptas sit aspernatur aut odit aut fugit</p>
    <p>Saed quia consequunturmagni dolorese seosasdqui ratione voluptatem sequi nesciunt. Neque porro quisquam est, qui dolorem ipsum quia dolor sit amet, consectetur, adipisci velit, sed quia non numquam eius modi tempora incidunt ut labore et dolore magnam aliquam quaerat voluptatem. Ut enim ad minima veniam, quis nostrum exercitationem ullam corporis suscipit laboriosam, nisi ut aliquid ex ea commodi consequatur.</p>
  </div>
  <div class="footer">www.nivelcrest.com</div><div class="page">Page 03</div>
</section>

<section class="slide s4">
  <h2 class="title">Our Team</h2>
  <div class="brand-mini"><i></i>Nivel Crest</div>
  <p class="lead">Caonsectetur adipiscing elitsed do eiusmod tempor incididuntut labore et dolore magna aliqua.<br>Utenimad minim veniam.</p>
  <div class="member" style="left:62px;top:70px" role="img" aria-label="Portrait of the CEO"><span class="name">Milo Varga<span class="role">CEO</span></span><span class="tag"></span></div>
  <div class="member" style="left:195px;top:70px" role="img" aria-label="Portrait of the VP Discovery"><span class="name">Teo Lindqvist<span class="role">VP Discovery</span></span><span class="tag"></span></div>
  <div class="member" style="left:328px;top:70px" role="img" aria-label="Portrait of the VP Development"><span class="name">Felix Durand<span class="role">VP Development</span></span><span class="tag"></span></div>
  <div class="member" style="left:62px;top:162px" role="img" aria-label="Portrait of the VP Regulatory"><span class="name">Jonas Albrecht<span class="role">VP Regulatory</span></span><span class="tag"></span></div>
  <div class="member" style="left:195px;top:162px" role="img" aria-label="Portrait of the senior director of marketing"><span class="name">Clara Moreau<span class="role">Sr. Director Marketing and Commercialization</span></span><span class="tag"></span></div>
  <div class="member" style="left:328px;top:162px" role="img" aria-label="Portrait of the chief technology officer"><span class="name">Lukas Brenner<span class="role">Chief Technology Officer</span></span><span class="tag"></span></div>
  <div class="footer">www.nivelcrest.com</div><div class="page">Page 04</div>
</section>

<section class="slide s5">
  <h2 class="title">Capacities and Present Workflows</h2>
  <div class="brand-mini"><i></i>Nivel Crest</div>
  <p class="lead">Caonsectetur adipiscing elitsed do eiusmod tempor incididuntut labore et dolore magna aliqua.<br>Utenimad minim veniam.</p>
  <svg class="flow" width="509" height="286" viewBox="0 0 509 286" aria-hidden="true">
    <g stroke="#bbb" stroke-width=".7" fill="none">
      <line x1="61" y1="155" x2="449" y2="155"/>
      <g stroke-dasharray="1.5 1.5">
        <line x1="61" y1="153" x2="61" y2="134"/><line x1="255" y1="153" x2="255" y2="134"/><line x1="449" y1="153" x2="449" y2="134"/>
        <line x1="158" y1="157" x2="158" y2="175"/><line x1="352" y1="157" x2="352" y2="175"/>
      </g>
    </g>
    <g fill="var(--gold)">
      <circle cx="61" cy="155" r="2"/><circle cx="158" cy="155" r="2"/><circle cx="255" cy="155" r="2"/><circle cx="352" cy="155" r="2"/><circle cx="449" cy="155" r="2"/>
    </g>
    <!-- gear -->
    <g transform="translate(61,184)" fill="var(--gold)">
      <circle r="9"/><rect x="-2.5" y="-13" width="5" height="26"/><rect x="-13" y="-2.5" width="26" height="5"/>
      <rect x="-2.5" y="-13" width="5" height="26" transform="rotate(45)"/><rect x="-2.5" y="-13" width="5" height="26" transform="rotate(-45)"/>
      <circle r="4" fill="#fff"/>
    </g>
    <!-- document -->
    <g transform="translate(158,126)">
      <rect x="-9" y="-12" width="18" height="24" rx="1.5" fill="var(--gold)"/>
      <g stroke="#fff" stroke-width="1.3"><line x1="-5" y1="-4" x2="5" y2="-4"/><line x1="-5" y1="0" x2="5" y2="0"/><line x1="-5" y1="4" x2="3" y2="4"/></g>
    </g>
    <!-- search -->
    <g transform="translate(255,184)" stroke="var(--gold)" fill="none" stroke-width="2.5">
      <circle cx="-3" cy="-3" r="8"/><line x1="3" y1="3" x2="11" y2="11" stroke-width="3.5" stroke-linecap="round"/>
    </g>
    <!-- chat -->
    <g transform="translate(352,124)" stroke="var(--gold)" fill="none" stroke-width="1.8">
      <path d="M-12 -9 H12 V6 H-2 L-7 11 V6 H-12 Z" stroke-linejoin="round"/>
      <line x1="-7" y1="-3" x2="7" y2="-3"/><line x1="-7" y1="1" x2="4" y2="1"/>
    </g>
    <!-- phone -->
    <g transform="translate(449,184)">
      <path d="M-10 -8 C-12 -2 -6 8 4 11 L8 7 L3 2 L0 4 C-3 2 -5 0 -6 -3 L-4 -6 L-8 -11 Z" fill="var(--gold)"/>
      <g stroke="var(--gold)" fill="none" stroke-width="1.3"><path d="M1 -6 A6 6 0 0 1 7 0"/><path d="M1 -10 A10 10 0 0 1 11 0"/></g>
    </g>
  </svg>
  <p class="flow-text" style="left:65px;top:101px">Faonsectetur adipisci velitsed quia non numquam eius modi tempora incidunt ut labore et dolore.</p>
  <p class="flow-text" style="left:259px;top:101px">Faonsectetur adipisci velitsed quia non numquam eius modi tempora incidunt ut labore et dolore.</p>
  <p class="flow-text" style="left:453px;top:101px">Faonsectetur adipisci velitsed quia non numquam eius modi tempora incidunt ut labore et dolore.</p>
  <p class="flow-text" style="left:158px;top:182px">Faonsectetur adipisci velitsed quia non numquam eius modi tempora incidunt ut labore et dolore.</p>
  <p class="flow-text" style="left:356px;top:182px;width:108px;margin-left:-54px">Faonsectetur adipisci velitsed quia non numquam eius modi tempora incidunt ut labore et dolore.</p>
  <div class="footer">www.nivelcrest.com</div><div class="page">Page 05</div>
</section>

<section class="slide s6">
  <h2 class="title">Organization Charts</h2>
  <div class="brand-mini"><i></i>Nivel Crest</div>
  <p class="lead">Caonsectetur adipiscing elitsed do eiusmod tempor incididuntut labore et dolore magna aliqua.<br>Utenimad minim veniam.</p>
  <div class="chart" style="left:107px">
    <svg width="100" height="94" viewBox="0 0 100 94" role="img" aria-label="74 percent ring chart">
      <ellipse cx="48" cy="84" rx="40" ry="5" fill="#000" opacity=".08"/>
      <circle cx="50" cy="44" r="36" fill="none" stroke="var(--ring)" stroke-width="8"/>
      <circle cx="50" cy="44" r="36" fill="none" stroke="var(--gold)" stroke-width="8" stroke-dasharray="167.4 226.2" transform="rotate(-90 50 44)"/>
      <text x="50" y="51" text-anchor="middle" font-family="Signika,sans-serif" font-weight="600" font-size="20" fill="#222">74%</text>
    </svg>
    <p>Serspiciatis undeomnis iste natus error sit voluptatem accusantium doloremque laudantium, totamrem aperiameaque ipsaquae ab illo inventore veritatis.</p>
  </div>
  <div class="chart" style="left:263px">
    <svg width="100" height="94" viewBox="0 0 100 94" role="img" aria-label="50 percent ring chart">
      <ellipse cx="48" cy="84" rx="40" ry="5" fill="#000" opacity=".08"/>
      <circle cx="50" cy="44" r="36" fill="none" stroke="var(--ring)" stroke-width="8"/>
      <circle cx="50" cy="44" r="36" fill="none" stroke="#d4913f" stroke-width="8" stroke-dasharray="113.1 226.2" transform="rotate(-90 50 44)"/>
      <text x="50" y="51" text-anchor="middle" font-family="Signika,sans-serif" font-weight="600" font-size="20" fill="#222">50%</text>
    </svg>
    <p>Serspiciatis undeomnis iste natus error sit voluptatem accusantium doloremque laudantium, totamrem aperiameaque ipsaquae ab illo inventore veritatis.</p>
  </div>
  <div class="chart" style="left:419px">
    <svg width="100" height="94" viewBox="0 0 100 94" role="img" aria-label="60 percent ring chart">
      <ellipse cx="48" cy="84" rx="40" ry="5" fill="#000" opacity=".08"/>
      <circle cx="50" cy="44" r="36" fill="none" stroke="var(--ring)" stroke-width="8"/>
      <circle cx="50" cy="44" r="36" fill="none" stroke="var(--gold-light)" stroke-width="8" stroke-dasharray="135.7 226.2" transform="rotate(-90 50 44)"/>
      <text x="50" y="51" text-anchor="middle" font-family="Signika,sans-serif" font-weight="600" font-size="20" fill="#222">60%</text>
    </svg>
    <p>Serspiciatis undeomnis iste natus error sit voluptatem accusantium doloremque laudantium, totamrem aperiameaque ipsaquae ab illo inventore veritatis.</p>
  </div>
  <div class="footer">www.nivelcrest.com</div><div class="page">Page 06</div>
</section>

</body>
</html>
```